Quillbrookes websites redesign

Www.quill-brookes.com needs to be redesigned along with updations. The incremental material will be provided for the updations. We are looking for complete redesign of the pages with the new content. The complete write up will be provided soon

Target Market(s)

Global

Coding

Coded - Design and coding required

Number of Pages Required

5+ page

Requirements
Must have
• A clean and slick design for the Consulting.
Should not have
• Too many pictures which reduces the speed of the site

```html
<!DOCTYPE html>
<html lang="en">
<head>
<meta charset="utf-8">
<title>Quillbrookes Consultancy</title>
<link href="https://fonts.googleapis.com/css2?family=Roboto:wght@300;400;500&display=swap" rel="stylesheet">
<style>
:root{
  --blue:#3ba8d3;
  --blue-dark:#2f97c2;
  --footer:#45b5de;
  --ink:#2b3541;
  --text:#555d66;
  --nav:#3a3f45;
  --white:#ffffff;
  --rule:#e6e8ea;
}
*{margin:0;padding:0;box-sizing:border-box}
html,body{width:754px;height:1200px;overflow:hidden;background:var(--white)}
body{font-family:'Roboto',sans-serif;color:var(--text);position:relative}
.abs{position:absolute}

.site-header{position:absolute;left:0;top:0;width:754px;height:53px;background:var(--white);border-bottom:1px solid var(--rule)}
.brand{left:46px;top:14px;display:flex;align-items:center;gap:8px}
.brand-mark{width:20px;height:20px;border-radius:50%;background:var(--blue)}
.brand-name{font-size:21px;font-weight:400;color:var(--ink);letter-spacing:.2px}
.nav a{position:absolute;top:27px;font-size:8px;color:var(--nav);text-decoration:none;letter-spacing:.3px;white-space:nowrap}
.nav a.active{color:var(--blue)}
.nav a.active::after{content:"";position:absolute;left:0;right:0;top:12px;height:2px;background:var(--blue)}
.nav-divider{left:686px;top:17px;width:1px;height:26px;background:var(--rule)}

.hero{left:0;top:53px;width:754px;height:295px;background:radial-gradient(ellipse at center,#ffffff 0%,#eef4f8 70%,#e2ecf3 100%)}
.hero-map{left:150px;top:40px;width:486px;height:240px;border-radius:40px;
  background:linear-gradient(120deg,#8a3ad0 0%,#e03a8c 30%,#f5452f 50%,#f7a21c 70%,#e8467c 100%);opacity:.9}

.about{left:0;top:348px;width:754px;text-align:center}
.section-title{font-size:17px;font-weight:400;color:var(--ink);letter-spacing:.2px}
.section-title span{color:var(--blue)}
.about .section-title{position:absolute;top:37px;width:754px}
.about p{position:absolute;left:70px;width:614px;font-size:8.3px;line-height:12.8px;color:var(--text)}
.btn{display:inline-block;background:var(--blue);color:var(--white);font-size:8.5px;letter-spacing:.3px;text-align:center;line-height:21px;height:21px;border-bottom:2px solid var(--blue-dark)}

.stats{left:0;top:556px;width:754px;height:226px;
  background:linear-gradient(180deg,#2a2522 0%,#4a3a30 45%,#2b2f38 75%,#1c1f26 100%)}
.stats-title{position:absolute;top:34px;width:754px;text-align:center;color:var(--white);font-size:17px;font-weight:400}
.stats-title small{font-size:11px}
.ring{position:absolute;top:79px;width:116px;height:116px}
.ring-label{position:absolute;inset:0;display:flex;align-items:center;justify-content:center;color:var(--white);font-size:18px}

.news-title{left:46px;top:822px}
.news-arrows{left:664px;top:823px;display:flex;gap:3px}
.news-arrows span{width:19px;height:16px;display:flex;align-items:center;justify-content:center}
.news-item{position:absolute;top:860px;width:203px}
.news-date{display:flex;align-items:center;gap:7px;font-size:18px;font-weight:300;color:var(--blue)}
.news-head{margin-top:5px;font-size:11.4px;font-weight:500;color:var(--ink);letter-spacing:.4px}
.news-text{margin-top:7px;font-size:8px;line-height:12.8px;text-align:justify}
.news-item .btn{margin-top:11px;width:82px}

.site-footer{left:0;top:1016px;width:754px;height:184px;background:var(--footer);color:var(--white)}
.f-title{position:absolute;top:33px;font-size:12.5px;font-weight:400;letter-spacing:.3px}
.f-email{position:absolute;left:46px;top:66px;width:152px;font-size:8.5px;border-bottom:1px solid var(--white);padding-bottom:4px}
.f-subscribe{position:absolute;left:46px;top:91px;width:152px;height:23px;background:var(--blue-dark);font-size:9.5px;text-align:center;line-height:23px}
.f-item{position:absolute;left:274px;display:flex;gap:10px;font-size:8.3px;line-height:12.8px}
.f-item svg{flex:none;margin-top:1px}
.social{position:absolute;left:514px;top:62px;display:flex;gap:3px}
.social span{width:27px;height:27px;border:1px solid var(--white);border-radius:50%}
.copyright{position:absolute;left:517px;top:109px;font-size:8.3px;line-height:12.8px}
</style>
</head>
<body>

<header class="site-header">
  <div class="abs brand"><span class="brand-mark"></span><span class="brand-name">Quillbrookes</span></div>
  <nav class="nav">
    <a class="active" style="left:296px">HOME</a>
    <a style="left:354px">FOUNDER</a>
    <a style="left:414px">CONSULTANCY</a>
    <a style="left:495px">SYSTEM</a>
    <a style="left:550px">CASE STUDIES</a>
    <a style="left:632px">CONTACT</a>
  </nav>
  <div class="abs nav-divider"></div>
  <svg class="abs" style="left:695px;top:27px" width="10" height="10" viewBox="0 0 10 10"><circle cx="4" cy="4" r="3" fill="none" stroke="#3a3f45" stroke-width="1.5"/><line x1="6.2" y1="6.2" x2="9" y2="9" stroke="#3a3f45" stroke-width="1.6"/></svg>
</header>

<section class="abs hero">
  <div class="abs hero-map" role="img" aria-label="Colourful watercolour world map"></div>
  <svg class="abs" style="left:48px;top:128px" width="18" height="30" viewBox="0 0 18 30"><polyline points="16,1 2,15 16,29" fill="none" stroke="#222" stroke-width="1.3"/></svg>
  <svg class="abs" style="left:686px;top:128px" width="18" height="30" viewBox="0 0 18 30"><polyline points="2,1 16,15 2,29" fill="none" stroke="#222" stroke-width="1.3"/></svg>
</section>

<section class="abs about">
  <h2 class="section-title">ABOUT <span>QUILLBROOKES CONSULTANCY</span></h2>
  <p style="top:68px">Quillbrookes Consultancy Limited capitalizes on synergies arising from trade and investment linkages between countries and knowledge of traditional and non-traditional pools of liquidity to provide consultancy services to Emerging country banks, Corporates and SMEs.</p>
  <p style="top:106px">The Consultancy provides bank neutral views to Corporates and SMEs in Asian emerging markets and helps in improving financial structure and efficient use of funds. Our endeavor is to provide a distinct bottom line advantage to our clients. The primary focus is in regionalisation of the banking relationship across the globe, providing structured finance solutions and off balance sheet solutions.</p>
  <a class="btn abs" style="left:336px;top:157px;width:82px">LEARN MORE</a>
</section>

<section class="abs stats" role="img" aria-label="Blurred city lights at dusk">
  <h2 class="stats-title">WORLD MERCHANDISING TRADE 2012 <small>(USD BILLION)</small></h2>
  <div class="ring" style="left:64px">
    <svg width="116" height="116" viewBox="0 0 116 116"><circle cx="58" cy="58" r="56" fill="none" stroke="rgba(255,255,255,.25)" stroke-width="3"/><path d="M58 2 A56 56 0 1 1 2 58 A56 56 0 0 1 58 2" fill="none" stroke="#fff" stroke-width="3"/></svg>
    <div class="ring-label">0-250</div>
  </div>
  <div class="ring" style="left:234px">
    <svg width="116" height="116" viewBox="0 0 116 116"><circle cx="58" cy="58" r="56" fill="none" stroke="rgba(255,255,255,.25)" stroke-width="3"/><path d="M58 2 A56 56 0 0 1 114 58" fill="none" stroke="#fff" stroke-width="3"/></svg>
    <div class="ring-label">250-500</div>
  </div>
  <div class="ring" style="left:404px">
    <svg width="116" height="116" viewBox="0 0 116 116"><circle cx="58" cy="58" r="56" fill="none" stroke="rgba(255,255,255,.25)" stroke-width="3"/><path d="M58 2 A56 56 0 1 1 8 83" fill="none" stroke="#fff" stroke-width="3"/></svg>
    <div class="ring-label">500-1000</div>
  </div>
  <div class="ring" style="left:570px">
    <svg width="116" height="116" viewBox="0 0 116 116"><circle cx="58" cy="58" r="56" fill="none" stroke="#fff" stroke-width="3"/></svg>
    <div class="ring-label">&gt;1000</div>
  </div>
</section>

<h2 class="abs section-title news-title">LATEST <span>NEWS</span></h2>
<div class="abs news-arrows">
  <span style="background:var(--blue)"><svg width="6" height="8" viewBox="0 0 6 8"><polyline points="5,1 1,4 5,7" fill="none" stroke="#fff" stroke-width="1.2"/></svg></span>
  <span style="background:#3a3f45"><svg width="6" height="8" viewBox="0 0 6 8"><polyline points="1,1 5,4 1,7" fill="none" stroke="#fff" stroke-width="1.2"/></svg></span>
</div>

<article class="news-item" style="left:47px">
  <div class="news-date"><svg width="16" height="16" viewBox="0 0 16 16"><rect x="1" y="2.5" width="14" height="12.5" fill="none" stroke="#3ba8d3" stroke-width="1.4"/><rect x="1" y="2.5" width="14" height="3" fill="#3ba8d3"/><g fill="#3ba8d3"><rect x="3.5" y="7.5" width="2" height="2"/><rect x="7" y="7.5" width="2" height="2"/><rect x="10.5" y="7.5" width="2" height="2"/><rect x="3.5" y="11" width="2" height="2"/><rect x="7" y="11" width="2" height="2"/><rect x="10.5" y="11" width="2" height="2"/></g></svg>25/05/2015</div>
  <h3 class="news-head">ESTABLISHING YOUR BRAND</h3>
  <p class="news-text">Sed ut perspiciatis unde omnis iste natus error sit voluptatem accusantium doloremque laudantium totam rem aperiam, eaque ipsa.</p>
  <a class="btn">LEARN MORE</a>
</article>
<article class="news-item" style="left:277px">
  <div class="news-date"><svg width="16" height="16" viewBox="0 0 16 16"><rect x="1" y="2.5" width="14" height="12.5" fill="none" stroke="#3ba8d3" stroke-width="1.4"/><rect x="1" y="2.5" width="14" height="3" fill="#3ba8d3"/><g fill="#3ba8d3"><rect x="3.5" y="7.5" width="2" height="2"/><rect x="7" y="7.5" width="2" height="2"/><rect x="10.5" y="7.5" width="2" height="2"/><rect x="3.5" y="11" width="2" height="2"/><rect x="7" y="11" width="2" height="2"/><rect x="10.5" y="11" width="2" height="2"/></g></svg>25/05/2015</div>
  <h3 class="news-head">ESTABLISHING YOUR BRAND</h3>
  <p class="news-text">Sed ut perspiciatis unde omnis iste natus error sit voluptatem accusantium doloremque laudantium totam rem aperiam, eaque ipsa.</p>
  <a class="btn">LEARN MORE</a>
</article>
<article class="news-item" style="left:502px">
  <div class="news-date"><svg width="16" height="16" viewBox="0 0 16 16"><rect x="1" y="2.5" width="14" height="12.5" fill="none" stroke="#3ba8d3" stroke-width="1.4"/><rect x="1" y="2.5" width="14" height="3" fill="#3ba8d3"/><g fill="#3ba8d3"><rect x="3.5" y="7.5" width="2" height="2"/><rect x="7" y="7.5" width="2" height="2"/><rect x="10.5" y="7.5" width="2" height="2"/><rect x="3.5" y="11" width="2" height="2"/><rect x="7" y="11" width="2" height="2"/><rect x="10.5" y="11" width="2" height="2"/></g></svg>25/05/2015</div>
  <h3 class="news-head">ESTABLISHING YOUR BRAND</h3>
  <p class="news-text">Sed ut perspiciatis unde omnis iste natus error sit voluptatem accusantium doloremque laudantium totam rem aperiam, eaque ipsa.</p>
  <a class="btn">LEARN MORE</a>
</article>

<footer class="abs site-footer">
  <h4 class="f-title" style="left:47px">SIGN UP FOR UPDATES</h4>
  <div class="f-email">Email</div>
  <div class="f-subscribe">Subscribe</div>

  <h4 class="f-title" style="left:274px">FIND US</h4>
  <div class="f-item" style="top:66px">
    <svg width="9" height="12" viewBox="0 0 9 12"><path d="M4.5 0A4.5 4.5 0 0 0 0 4.5C0 8 4.5 12 4.5 12S9 8 9 4.5A4.5 4.5 0 0 0 4.5 0Z" fill="#fff"/><circle cx="4.5" cy="4.5" r="1.7" fill="#45b5de"/></svg>
    <div>4120 Harbour Lane, Westfield<br>Glasgow, G12 7QX.</div>
  </div>
  <div class="f-item" style="top:104px">
    <svg width="11" height="11" viewBox="0 0 11 11"><rect x="0" y="2" width="11" height="9" rx="1" fill="#fff"/><rect x="2" y="0" width="5" height="4" fill="#fff" stroke="#45b5de" stroke-width=".8"/><g fill="#45b5de"><rect x="5" y="5" width="1.5" height="1.5"/><rect x="7.5" y="5" width="1.5" height="1.5"/><rect x="5" y="7.5" width="1.5" height="1.5"/><rect x="7.5" y="7.5" width="1.5" height="1.5"/><rect x="1.5" y="4.5" width="2" height="5"/></g></svg>
    <div>Telephone: +1 555 014 2270<br>FAX: +1 555 018 3341</div>
  </div>
  <div class="f-item" style="top:142px">
    <svg width="10" height="8" viewBox="0 0 10 8"><rect width="10" height="8" fill="#fff"/><polyline points="0,0 5,4.5 10,0" fill="none" stroke="#45b5de" stroke-width="1"/></svg>
    <div>E-mail: hello@quill-brookes.com</div>
  </div>

  <h4 class="f-title" style="left:514px">KEEP IN TOUCH</h4>
  <div class="social"><span></span><span></span><span></span><span></span><span></span></div>
  <p class="copyright">© Quillbrookes Consultancy Limited,<br>All Right Reserved.</p>
</footer>

</body>
</html>
```